Weightloss company needs Business Card

We want a business card that is clean and professional, yet portrays that we are a friendly, innovative, and versatile program designed to fit the needs of our clients.
I would like there to be 2 sides, one side having an appointment card, and the other side containing the logo and business information. There can be decorations on both sides. The logo is attached.

Target Market(s)

Men and women 40-60

Industry/Entity Type

Business

Contact Information for Business Card

Font styles to use
Sans Serif

Requirements
Must have
• The logo, space for business information
Nice to have
• The colors in the logo
Should not have
• No pictures of people or food

```html
<!DOCTYPE html>
<html lang="en">
<head>
<meta charset="utf-8">
<title>Renewly Wellness – Business Card</title>
<link href="https://fonts.googleapis.com/css2?family=Questrial&display=swap" rel="stylesheet">
<style>
  :root {
    --backdrop: #3a3a3c;
    --card: #ffffff;
    --ink: #111111;
    --band: #050505;
    --brand-red: #d8202f;
    --accent-cyan: #3fb6e3;
    --rule: #222222;
    --light-text: #ffffff;
  }
  * { box-sizing: border-box; margin: 0; padding: 0; }
  html, body {
    width: 1200px; height: 900px; overflow: hidden;
    background: var(--backdrop);
    font-family: "Questrial", "Century Gothic", sans-serif;
  }
  .canvas {
    position: relative; width: 1200px; height: 900px;
  }
  .card {
    position: absolute; width: 640px; height: 366px;
    background: var(--card); border-radius: 22px; overflow: hidden;
    box-shadow: 0 14px 30px rgba(0,0,0,.45);
  }
  .card--appointment { left: 120px; top: 60px; }
  .card--contact { left: 440px; top: 474px; }

  .brand {
    position: absolute; display: flex; align-items: center; gap: 10px;
    color: var(--brand-red); font-size: 30px; letter-spacing: .5px;
  }
  .brand__dot {
    width: 14px; height: 14px; border-radius: 50%; background: var(--brand-red);
  }
  .card--appointment .brand { left: 48px; top: 70px; }
  .card--contact .brand { left: 48px; top: 62px; }

  .appointment {
    position: absolute; left: 48px; top: 168px; right: 60px;
  }
  .appointment__title {
    color: var(--accent-cyan); font-size: 17px; letter-spacing: .5px;
    text-transform: uppercase; margin-bottom: 14px;
  }
  .appointment__row {
    display: flex; align-items: flex-end; gap: 10px;
    font-size: 18px; color: var(--ink); height: 42px;
  }
  .appointment__line {
    flex: 1; border-bottom: 1.5px solid var(--rule); margin-bottom: 5px;
  }

  .band { position: absolute; inset: 0; }

  .person {
    position: absolute; left: 48px; top: 196px; color: var(--light-text);
  }
  .person__name {
    color: var(--accent-cyan); font-size: 28px; letter-spacing: 1px;
    text-transform: uppercase; font-weight: 700;
  }
  .person__role {
    font-size: 15px; letter-spacing: 1px; text-transform: uppercase;
    margin: 4px 0 14px 2px;
  }
  .person__address { font-size: 16px; line-height: 1.35; }

  .contact {
    position: absolute; left: 360px; top: 196px; list-style: none;
    color: var(--light-text); font-size: 15.5px;
  }
  .contact li { display: flex; align-items: center; gap: 10px; height: 26px; }
  .contact svg { width: 14px; height: 14px; flex: none; }
</style>
</head>
<body>
<main class="canvas">

  <section class="card card--appointment" aria-label="Appointment side">
    <div class="brand"><span class="brand__dot"></span>Renewly Wellness</div>
    <div class="appointment">
      <p class="appointment__title">Appointment</p>
      <div class="appointment__row"><span>Name:</span><span class="appointment__line"></span></div>
      <div class="appointment__row"><span>Date:</span><span class="appointment__line"></span></div>
      <div class="appointment__row"><span>Time:</span><span class="appointment__line"></span></div>
    </div>
  </section>

  <section class="card card--contact" aria-label="Contact side">
    <svg class="band" viewBox="0 0 640 366" preserveAspectRatio="none" aria-hidden="true">
      <path d="M0 172 H450 C478 172 488 48 578 42 C622 40 640 70 640 92 V326 H0 Z" fill="var(--band)"/>
    </svg>
    <div class="brand"><span class="brand__dot"></span>Renewly Wellness</div>

    <div class="person">
      <p class="person__name">Marcus Hale</p>
      <p class="person__role">Director</p>
      <p class="person__address">Palm Avenue, 21400<br>Harbor City, Coastland</p>
    </div>

    <ul class="contact">
      <li>
        <svg viewBox="0 0 24 24" fill="var(--accent-cyan)"><path d="M6.6 10.8a15.1 15.1 0 0 0 6.6 6.6l2.2-2.2c.3-.3.7-.4 1-.2 1.1.4 2.3.6 3.6.6.6 0 1 .4 1 1V20c0 .6-.4 1-1 1C10.6 21 3 13.4 3 4c0-.6.4-1 1-1h3.5c.6 0 1 .4 1 1 0 1.3.2 2.5.6 3.6.1.3 0 .7-.2 1z"/></svg>
        +330 5550-1234
      </li>
      <li>
        <svg viewBox="0 0 24 24" fill="none" stroke="var(--accent-cyan)" stroke-width="2"><rect x="3" y="5" width="18" height="14" rx="1"/><path d="M3 6l9 7 9-7"/></svg>
        hello@renewlywellness.com
      </li>
      <li>
        <svg viewBox="0 0 24 24" fill="none" stroke="var(--accent-cyan)" stroke-width="2"><circle cx="12" cy="12" r="9"/><path d="M3 12h18M12 3c3 3 3 15 0 18M12 3c-3 3-3 15 0 18"/></svg>
        www.renewlywellness.com
      </li>
    </ul>
  </section>

</main>
</body>
</html>
```